Vorlanta PowerPoint Template

I have a company called Vorlanta, LLC and my company logo is already designed. I need a PowerPoint template that I will be using to pitch potential investors and business partners. This should be a very professional-looking template that leverages the company logo colors and really pops. The company is an AI product research and development company.

```html
<!DOCTYPE html>
<html lang="en">
<head>
<meta charset="utf-8">
<title>Vorlanta Pitch Template</title>
<link rel="stylesheet" href="https://fonts.googleapis.com/css2?family=Lato:wght@400;700&display=swap">
<style>
:root{
  --red:#b0141f;
  --red-deep:#8e0d17;
  --charcoal:#3b3b3d;
  --ink:#2e2e30;
  --navy:#2a2d35;
  --text:#3a3a3a;
  --white:#ffffff;
}
*{box-sizing:border-box;margin:0;padding:0}
html,body{width:1050px;height:1200px;overflow:hidden;background:#fff}
body{font-family:'Lato',sans-serif;color:var(--text);position:relative}
.slide{position:absolute;width:774px;height:435px;background:var(--white);overflow:hidden;
  transform:scale(0.5866);transform-origin:0 0;box-shadow:0 0 6px rgba(0,0,0,.18)}
.abs{position:absolute}
.photo{position:absolute}
.page-no{position:absolute;top:12px;right:12px;font-size:12px;color:var(--ink)}
.brand{position:absolute;display:flex;align-items:center;gap:8px}
.brand-dot{border-radius:50%;background:var(--red)}
.brand-name{font-weight:700;color:var(--ink);letter-spacing:-.5px}
.brand.sm .brand-dot{width:36px;height:36px}
.brand.sm .brand-name{font-size:31px}
.brand.lg .brand-dot{width:58px;height:58px}
.brand.lg .brand-name{font-size:50px}
.heading{position:absolute;font-size:34px;line-height:1.2;color:var(--ink);font-weight:400}
.heading .hl{color:var(--red);font-weight:700}
.rule{position:absolute;height:3px;width:80px;background:var(--ink)}
.rule.light{background:var(--white)}
.body{position:absolute;font-size:12px;line-height:1.5;color:var(--text)}
.strip-dark{position:absolute;left:0;width:22px;background:var(--charcoal)}
.band-red{position:absolute;background:var(--red)}
.icon-box{position:absolute;width:80px;height:77px;background:var(--white);display:flex;align-items:center;justify-content:center}
.svc-title{position:absolute;font-size:14px;font-weight:700;color:var(--white)}
.svc-desc{position:absolute;font-size:12px;line-height:1.4;color:#e6e6e6;width:220px}
.member{position:absolute;top:162px;width:217px}
.member .photo{position:relative;height:178px}
.member .label{background:var(--red);height:65px;color:var(--white);text-align:center;padding-top:11px}
.member .name{font-size:17px;font-weight:700}
.member .role{font-size:13px}
.feature{position:absolute;top:248px;width:240px;text-align:center;color:var(--white)}
.feature .icon-box{position:relative;margin:0 auto}
.feature h3{font-size:14px;font-weight:700;margin-top:14px}
.feature p{font-size:12px;line-height:1.4;margin-top:10px;color:#e6e6e6}
.contact{position:absolute;display:flex;align-items:center;gap:12px;font-size:12px;font-weight:700;color:var(--ink);line-height:1.35}
.contact-icon{width:40px;height:40px;border-radius:50%;background:var(--red);display:flex;align-items:center;justify-content:center}
</style>
</head>
<body>

<!-- Cover -->
<section class="slide" style="left:51px;top:41px">
  <div class="strip-dark" style="top:375px;height:60px"></div>
  <div class="band-red" style="left:22px;right:0;top:375px;height:60px"></div>
  <div class="photo" role="img" aria-label="Photo of a smiling professional holding a laptop in an office" style="left:45px;top:26px;width:303px;height:409px;background:linear-gradient(160deg,#55606b,#222a33 60%,#1a1d22)"></div>
  <div class="brand lg" style="left:403px;top:28px"><span class="brand-dot"></span><span class="brand-name">Vorlanta</span></div>
  <h1 class="heading" style="left:411px;top:118px">AI Product Research<br>&amp; <span class="hl">Development<br>Company</span></h1>
  <div class="rule" style="left:415px;top:252px"></div>
  <p class="body" style="left:411px;top:270px;width:330px">Designing and engineering advanced AI products that are scalable, customizable, and market-ready. We bridge the gap between cutting-edge research and real-world application—delivering rapid, tailored AI solutions for forward-thinking businesses.</p>
</section>

<!-- Services -->
<section class="slide" style="left:50px;top:329px">
  <div class="brand sm" style="left:16px;top:17px"><span class="brand-dot"></span><span class="brand-name">Vorlanta</span></div>
  <div class="page-no">Page 02</div>
  <h2 class="heading" style="left:0;right:0;top:30px;text-align:center">Our <span class="hl">Services</span></h2>
  <div class="rule" style="left:347px;top:80px"></div>
  <p class="body" style="left:0;right:0;top:100px;text-align:center">Vorlanta delivers cutting-edge AI innovation through flexible, scalable,<br>and deeply customized service offerings.</p>
  <div class="abs" role="img" aria-label="Dark background of hands working with digital AI interface" style="left:0;top:170px;width:774px;height:265px;background:linear-gradient(120deg,#2a2d35,#353a44 50%,#262930)"></div>

  <div class="icon-box" style="left:51px;top:210px"><svg width="54" height="54" viewBox="0 0 54 54" fill="none" stroke="#b0141f" stroke-width="2"><rect x="12" y="12" width="30" height="30"/><text x="27" y="32" font-family="Lato,sans-serif" font-size="12" fill="#b0141f" stroke="none" text-anchor="middle" font-weight="700">AI</text><path d="M18 12V4M27 12V4M36 12V4M18 42v8M27 42v8M36 42v8M12 18H4M12 27H4M12 36H4M42 18h8M42 27h8M42 36h8"/></svg></div>
  <div class="svc-title" style="left:158px;top:216px">AI Product Development</div>
  <div class="svc-desc" style="left:158px;top:242px">Custom AI solutions from concept to deployment.</div>

  <div class="icon-box" style="left:427px;top:210px"><svg width="54" height="54" viewBox="0 0 54 54" fill="none" stroke="#b0141f" stroke-width="2"><circle cx="27" cy="27" r="11"/><path d="M21 27l4 4 8-8"/><path d="M27 4v8M27 42v8M4 27h8M42 27h8M11 11l6 6M37 37l6 6M43 11l-6 6M17 37l-6 6"/></svg></div>
  <div class="svc-title" style="left:534px;top:218px">Scalable AI Toolkits &amp; APIs</div>
  <div class="svc-desc" style="left:534px;top:244px">We offer modular, production-ready components for fast AI adoption.</div>

  <div class="icon-box" style="left:51px;top:318px"><svg width="54" height="54" viewBox="0 0 54 54" fill="none" stroke="#b0141f" stroke-width="2"><rect x="6" y="8" width="40" height="28"/><path d="M20 36l-3 8h18l-3-8"/><circle cx="38" cy="34" r="7"/><path d="M43 39l6 6M12 16h14M12 22h10"/></svg></div>
  <div class="svc-title" style="left:158px;top:326px">AI Research &amp; Prototyping</div>
  <div class="svc-desc" style="left:158px;top:352px">We explore new concepts, validate ideas, and rapidly build working prototypes.</div>

  <div class="icon-box" style="left:427px;top:318px"><svg width="54" height="54" viewBox="0 0 54 54" fill="none" stroke="#b0141f" stroke-width="2"><path d="M4 22l10-8 10 4 8-4 10 2 8 8-18 18-6-4-6-2-16-14z"/><path d="M24 18l-6 8 4 2 8-6M27 4v6M18 6l3 5M36 6l-3 5"/></svg></div>
  <div class="svc-title" style="left:534px;top:326px">Strategic AI Partnerships</div>
  <div class="svc-desc" style="left:534px;top:352px">We collaborate with companies to co-develop next-gen AI products.</div>
</section>

<!-- About -->
<section class="slide" style="left:51px;top:616px">
  <div class="brand sm" style="left:16px;top:17px"><span class="brand-dot"></span><span class="brand-name">Vorlanta</span></div>
  <h2 class="heading" style="left:20px;top:85px">About <span class="hl">Vorlanta</span></h2>
  <div class="rule" style="left:20px;top:134px"></div>
  <p class="body" style="left:20px;top:155px;width:310px"><strong style="color:var(--red)">Vorlanta is an AI product research and development company</strong> that transforms cutting-edge ideas into scalable, real-world AI solutions.</p>
  <p class="body" style="left:20px;top:230px;width:345px">We specialize in bridging the gap between academic innovation and practical application. Our team of AI engineers, researchers, and product strategists builds custom tools, APIs, and platforms that help companies unlock the true potential of artificial intelligence—faster and with less friction.</p>
  <div class="strip-dark" style="top:375px;height:60px"></div>
  <div class="band-red" style="left:22px;width:380px;top:375px;height:60px"></div>
  <div class="contact" style="left:94px;top:385px;color:var(--white);font-size:14px;font-weight:400">
    <span class="contact-icon" style="background:var(--white)"><svg width="20" height="20" viewBox="0 0 24 24" fill="#b0141f"><path d="M6.6 10.8a15.1 15.1 0 006.6 6.6l2.2-2.2c.3-.3.7-.4 1-.2 1.1.4 2.3.6 3.6.6.6 0 1 .4 1 1V20c0 .6-.4 1-1 1C10.6 21 3 13.4 3 4c0-.6.4-1 1-1h3.5c.6 0 1 .4 1 1 0 1.3.2 2.5.6 3.6.1.3 0 .7-.2 1z"/></svg></span>
    <span>Call US :&nbsp; + 1 555 010 4420</span>
  </div>
  <div class="photo" role="img" aria-label="Hand holding a glowing network of AI technology icons" style="left:402px;top:0;width:372px;height:435px;background:radial-gradient(circle at 55% 45%,#3f6d9a,#1c2f4d 45%,#0f1829)"></div>
  <div class="page-no" style="color:var(--white)">Page 03</div>
</section>

<!-- Team -->
<section class="slide" style="left:51px;top:903px">
  <div class="brand sm" style="left:16px;top:17px"><span class="brand-dot"></span><span class="brand-name">Vorlanta</span></div>
  <div class="page-no">Page 04</div>
  <h2 class="heading" style="left:0;right:0;top:30px;text-align:center">Our <span class="hl">Team</span></h2>
  <div class="rule" style="left:347px;top:80px"></div>
  <p class="body" style="left:0;right:0;top:100px;text-align:center">A world-class team of AI innovators, product builders, and<br>business strategists.</p>
  <div class="member" style="left:32px"><div class="photo" role="img" aria-label="Portrait of the founder and CEO" style="background:linear-gradient(180deg,#9a9488,#4b4a4c 60%,#26272b)"></div><div class="label"><div class="name">Marcus Dell</div><div class="role">Founder &amp; CEO</div></div></div>
  <div class="member" style="left:279px"><div class="photo" role="img" aria-label="Portrait of the chief technology officer" style="background:linear-gradient(180deg,#8e8e8e,#6a625c 60%,#cdbba4)"></div><div class="label"><div class="name">Sofia Lenn</div><div class="role">Chief Technology Officer</div></div></div>
  <div class="member" style="left:525px"><div class="photo" role="img" aria-label="Portrait of the AI advisor" style="background:linear-gradient(180deg,#6f7478,#3a3f46 60%,#1f2329)"></div><div class="label"><div class="name">Adrian Voss</div><div class="role">AI Advisor</div></div></div>
</section>

<!-- Why -->
<section class="slide" style="left:547px;top:41px">
  <div class="brand sm" style="left:16px;top:17px"><span class="brand-dot"></span><span class="brand-name">Vorlanta</span></div>
  <div class="page-no">Page 05</div>
  <h2 class="heading" style="left:21px;top:72px">Why <span class="hl">Vorlanta?</span></h2>
  <div class="rule" style="left:21px;top:112px;width:70px;height:2px"></div>
  <p class="body" style="left:21px;top:145px;width:270px">Delivering high-impact, low-friction AI solutions built for real-world value.</p>
  <p class="body" style="left:364px;top:76px;width:390px">We combine cutting-edge research with agile product development to bring AI from concept to execution—fast. Our solutions are purpose-built, highly adaptable, and designed to solve real business problems with measurable outcomes. Whether you're launching a new AI product or embedding intelligence into existing systems, Vorlanta delivers speed, precision, and long-term scalability.</p>
  <div class="photo" role="img" aria-label="Illustration of a humanoid robot in profile with glowing neural lines" style="left:0;top:218px;width:254px;height:217px;background:radial-gradient(circle at 60% 50%,#3a4f7a,#141a2e 60%,#0a0d18)"></div>
  <div class="abs" style="left:254px;top:218px;width:520px;height:217px;background:var(--charcoal)"></div>
  <div class="feature" style="left:273px">
    <div class="icon-box"><svg width="50" height="50" viewBox="0 0 50 50" fill="none" stroke="#b0141f" stroke-width="2"><circle cx="25" cy="25" r="13"/><path d="M25 4v7M25 39v7M4 25h7M39 25h7M10 10l5 5M35 35l5 5M40 10l-5 5M15 35l-5 5M18 30l5-5 3 3 6-7"/></svg></div>
    <h3>Speed with Precision</h3>
    <p>We turn AI concepts into functional products in weeks—without compromising quality or scalability.</p>
  </div>
  <div class="feature" style="left:518px">
    <div class="icon-box"><svg width="50" height="50" viewBox="0 0 50 50" fill="none" stroke="#b0141f" stroke-width="2"><path d="M42 8c-12 0-20 8-24 18l6 6c10-4 18-12 18-24z"/><circle cx="32" cy="18" r="3"/><path d="M18 26l-8 2 4-8 8-2M24 32l-2 8 8-4 2-8M14 36l-6 6M18 40l-4 4M10 32l-4 4"/></svg></div>
    <h3>Custom-Built for Impact</h3>
    <p>Solutions are tailored to the client's unique needs—not generic, off-the-shelf tools.</p>
  </div>
</section>

<!-- AI Development Company -->
<section class="slide" style="left:547px;top:329px">
  <div class="abs" style="left:0;top:0;width:543px;height:435px;background:linear-gradient(135deg,#a8121d,#b8161f 50%,#8e0d17)"></div>
  <div class="abs" style="left:543px;top:0;width:231px;height:435px;background:var(--charcoal)"></div>
  <h2 class="heading" style="left:57px;top:100px;color:var(--white);font-weight:700">AI Development<br>Company</h2>
  <div class="rule light" style="left:60px;top:203px"></div>
  <p class="body" style="left:57px;top:228px;width:320px;color:var(--white)">Vorlanta is a specialized AI product development company focused on turning bold ideas into intelligent, scalable solutions. We build end-to-end AI systems—from model design and training to full-stack application deployment—customized to meet the unique needs of startups, enterprises, and innovation teams.</p>
  <div class="photo" role="img" aria-label="Photo of two colleagues reviewing documents at a meeting table" style="left:434px;top:20px;width:316px;height:395px;background:linear-gradient(170deg,#9aa4a2,#6d7270 45%,#d8dcdc)"></div>
</section>

<!-- Product Research -->
<section class="slide" style="left:547px;top:616px">
  <div class="abs" style="left:40px;top:0;width:310px;height:322px;background:var(--red)"></div>
  <div class="photo" role="img" aria-label="Photo of developers working at computer screens in a bright office" style="left:0;top:54px;width:296px;height:381px;background:linear-gradient(160deg,#c9cfcf,#8a8f92 50%,#4a4c50)"></div>
  <div class="page-no">Page 07</div>
  <h2 class="heading" style="left:411px;top:60px">AI Product <span class="hl">Research</span></h2>
  <div class="rule" style="left:411px;top:108px"></div>
  <p class="body" style="left:411px;top:128px;width:320px;font-weight:700;color:var(--red)">Driving innovation at the intersection of AI theory and real-world application.</p>
  <p class="body" style="left:411px;top:188px;width:335px">At Vorlanta, our core strength lies in transforming cutting-edge AI research into commercially viable products. We explore and experiment with the latest advancements in machine learning, large language models (LLMs), and generative AI to uncover innovative solutions to real-world challenges.</p>
  <p class="body" style="left:411px;top:293px;width:335px">Our research focuses on both foundational model development and practical enhancements—such as fine-tuning, optimization, and domain-specific adaptation. By combining academic rigor with product-driven thinking, we ensure that every insight we generate contributes directly to scalable, high-impact applications.</p>
</section>

<!-- Thank You -->
<section class="slide" style="left:547px;top:903px">
  <div class="strip-dark" style="top:375px;height:60px"></div>
  <div class="band-red" style="left:22px;right:0;top:375px;height:60px"></div>
  <div class="photo" role="img" aria-label="Illustration of a robotic hand beneath a glowing red AI chip" style="left:45px;top:26px;width:303px;height:409px;background:radial-gradient(circle at 70% 30%,#7a1a22,#1b2a4a 45%,#0b1226)"></div>
  <div class="page-no">Page 08</div>
  <div class="brand lg" style="left:403px;top:28px"><span class="brand-dot"></span><span class="brand-name">Vorlanta</span></div>
  <h2 class="heading" style="left:411px;top:122px">Thank <span class="hl">You</span></h2>
  <div class="rule" style="left:415px;top:182px"></div>
  <p class="body" style="left:411px;top:200px;font-size:14px;line-height:1.45"><strong style="color:var(--red)">Vorlanta, LLC</strong><br>Igniting the Future with AI</p>
  <div class="contact" style="left:403px;top:268px">
    <span class="contact-icon"><svg width="20" height="20" viewBox="0 0 24 24" fill="#fff"><path d="M6.6 10.8a15.1 15.1 0 006.6 6.6l2.2-2.2c.3-.3.7-.4 1-.2 1.1.4 2.3.6 3.6.6.6 0 1 .4 1 1V20c0 .6-.4 1-1 1C10.6 21 3 13.4 3 4c0-.6.4-1 1-1h3.5c.6 0 1 .4 1 1 0 1.3.2 2.5.6 3.6.1.3 0 .7-.2 1z"/></svg></span>
    <span>Call US :<br>+ 1 555 010 4420</span>
  </div>
  <div class="contact" style="left:576px;top:268px">
    <span class="contact-icon"><svg width="20" height="20" viewBox="0 0 24 24" fill="#fff"><path d="M3 5h18v14H3z" opacity="0"/><path d="M3 6h18v12H3V6zm2 1.5v.3l7 5 7-5v-.3H5z"/></svg></span>
    <span>Email :<br>info@Vorlanta.com</span>
  </div>
</section>

</body>
</html>
```